Locksmith Business Cards

My father-in-law is in need of new business cards for his locksmith business and I need to impress him. Kindly help me out!

You can see the previous business card attached. It is a family run business in North Wales.

No individual names on the cards.

Key Things to Feature:
- The words "Prompt", "Local", "Reliable" (as you can see under the logo on the website)
- 24h Emergency Service
- Covering All of North Wales, the Wirral and Chester
- The color blue
- A key or a lock would be interesting (similar to the ones that come up when you google locksmith business card)

Optional (only if design includes bullet points, like the example below):
https://imgvaultcdn.net/samples/208314/55172/55172_3904821_208314_image.jpg
- Residential / Commercial / Automotive
- Alarms & Cameras
- Key Cutting & Safes

https://www.brynhafod-locksmiths.co.uk/

Industry/Entity Type

Locksmith

Contact Information for Business Card

01632 960 418
07700 900 362
brynhafodlocksmiths@mailvane.com
Brynhafod Locksmiths, The Willow Barn, 7 Tannery Rd., Llandudno LL99 4QX
www.brynhafod-locksmiths.co.uk

Requirements
Must have
• - The words "Prompt", "Local", "Reliable" (as you can see under the logo on the website)
• - 24h Emergency Service
• - Covering All of North Wales, the Wirral and Chester
Nice to have
• - A key or a lock would be interesting (similar to the ones that come up when you google locksmith business card)

```html
<!DOCTYPE html>
<html lang="en">
<head>
<meta charset="utf-8">
<title>Brynhafod Locksmiths – Business Cards</title>
<link href="https://fonts.googleapis.com/css2?family=Oswald:wght@500&family=Open+Sans:wght@400;600;700&display=swap" rel="stylesheet">
<style>
  :root {
    --bg: #e6e6e8;
    --paper: #f7f7f7;
    --navy: #1f2a6e;
    --navy-deep: #1b2566;
    --blue: #2e3a8c;
    --ink: #3a3a44;
    --rule: #c9c9d2;
    --white: #ffffff;
    --faint: rgba(255,255,255,0.10);
    --faint-navy: rgba(46,58,140,0.08);
  }
  * { box-sizing: border-box; margin: 0; padding: 0; }
  html, body {
    width: 1200px; height: 844px; overflow: hidden;
    background: var(--bg);
    font-family: "Open Sans", Arial, sans-serif;
  }
  .sheet { position: relative; width: 1200px; height: 844px; }
  .card {
    position: absolute; top: 262px;
    width: 530px; height: 320px;
    border-radius: 4px;
    overflow: hidden;
    box-shadow: 0 6px 18px rgba(0,0,0,0.18);
  }
  .card--front { left: 55px; background: var(--paper); color: var(--ink); }
  .card--back { left: 615px; background: var(--navy); color: var(--white); }

  .decor-circle {
    position: absolute; right: -40px; top: 40px;
    width: 200px; height: 200px; border-radius: 50%;
  }
  .card--front .decor-circle { background: var(--faint-navy); }
  .card--back .decor-circle { background: var(--faint); right: 20px; top: 20px; width: 150px; height: 150px; }

  /* Front */
  .brand { position: absolute; left: 34px; top: 40px; display: flex; align-items: center; gap: 12px; }
  .brand__mark { width: 46px; height: 46px; background: var(--navy); border-radius: 6px; }
  .brand__name {
    font-family: "Oswald", "Arial Narrow", sans-serif; font-weight: 500;
    font-size: 30px; line-height: 30px; color: var(--navy); text-transform: uppercase; letter-spacing: 0.5px;
  }
  .contacts { position: absolute; left: 34px; top: 122px; list-style: none; font-size: 14px; line-height: 19px; }
  .contacts li { display: flex; align-items: center; gap: 7px; }
  .contacts svg { width: 12px; height: 12px; fill: var(--navy); flex: none; }
  .rule { position: absolute; left: 34px; width: 330px; height: 1px; background: var(--rule); }
  .rule--a { top: 206px; }
  .rule--b { top: 254px; }
  .address { position: absolute; left: 34px; top: 212px; font-size: 14px; line-height: 19px; }
  .service { position: absolute; left: 34px; top: 260px; font-size: 14px; line-height: 19px; }
  .service__title { color: var(--navy); font-weight: 700; text-transform: uppercase; }

  /* Back */
  .back-brand {
    position: absolute; left: 50px; top: 78px;
    font-family: "Oswald", "Arial Narrow", sans-serif; font-weight: 500;
    font-size: 34px; line-height: 36px; text-transform: uppercase;
  }
  .tagline { position: absolute; left: 50px; top: 158px; font-size: 12px; font-weight: 700; letter-spacing: 0.8px; }
  .services { position: absolute; left: 50px; top: 212px; list-style: none; font-size: 14px; line-height: 22px; }
  .services li::before { content: "●"; font-size: 9px; margin-right: 7px; vertical-align: 2px; }
</style>
</head>
<body>
<main class="sheet">
  <section class="card card--front" aria-label="Business card front">
    <div class="decor-circle" aria-hidden="true"></div>
    <div class="brand">
      <div class="brand__mark" aria-hidden="true"></div>
      <div class="brand__name">Brynhafod<br>Locksmiths</div>
    </div>
    <ul class="contacts">
      <li><svg viewBox="0 0 24 24"><path d="M6.6 10.8a15 15 0 0 0 6.6 6.6l2.2-2.2c.3-.3.7-.4 1-.2 1.1.4 2.3.6 3.6.6.6 0 1 .4 1 1V20c0 .6-.4 1-1 1A17 17 0 0 1 3 4c0-.6.4-1 1-1h3.5c.6 0 1 .4 1 1 0 1.3.2 2.5.6 3.6.1.3 0 .7-.2 1z"/></svg>01632 960 418</li>
      <li><svg viewBox="0 0 24 24"><path d="M7 1h10a2 2 0 0 1 2 2v18a2 2 0 0 1-2 2H7a2 2 0 0 1-2-2V3a2 2 0 0 1 2-2zm0 3v14h10V4z"/></svg>07700 900 362</li>
      <li><svg viewBox="0 0 24 24"><path d="M2 5h20v14H2zm2 2v.5l8 5 8-5V7l-8 5z"/></svg>brynhafodlocksmiths@mailvane.com</li>
      <li><svg viewBox="0 0 24 24"><path d="M12 2a10 10 0 1 0 0 20 10 10 0 0 0 0-20zm-1 17.9A8 8 0 0 1 4.1 11H8c.1 3 1.1 6.4 3 8.9zM8 9H4.1A8 8 0 0 1 11 4.1C9.1 6.6 8.1 9 8 9zm2 0c.2-2 .9-3.7 2-5.3 1.1 1.6 1.8 3.3 2 5.3zm0 2h4c-.2 2.6-.9 4.9-2 6.6-1.1-1.7-1.8-4-2-6.6zm6 0h3.9a8 8 0 0 1-6.9 8.9c1.9-2.5 2.9-5.9 3-8.9zm0-2c-.1 0-1.1-2.4-3-4.9A8 8 0 0 1 19.9 9z"/></svg>www.brynhafod-locksmiths.co.uk</li>
    </ul>
    <div class="rule rule--a"></div>
    <p class="address">Brynhafod Locksmiths, The Willow Barn, 7 Tannery Rd.,<br>Llandudno LL99 4QX</p>
    <div class="rule rule--b"></div>
    <p class="service"><span class="service__title">24h Emergency Service</span><br>Covering All of North Wales, the Wirral and Chester</p>
  </section>

  <section class="card card--back" aria-label="Business card back">
    <div class="decor-circle" aria-hidden="true"></div>
    <h1 class="back-brand">Brynhafod<br>Locksmiths</h1>
    <p class="tagline">PROMPT. LOCAL. RELIABLE</p>
    <ul class="services">
      <li>Residential / Commercial / Automotive</li>
      <li>Alarms &amp; Cameras</li>
      <li>Key Cutting &amp; Safes</li>
    </ul>
  </section>
</main>
</body>
</html>
```